Food Label: GlowMallo - IMO - Isomalto-oligosaccharides syrup

GlowMallo is a thick, syrupy liquid soluble pre-biotic fiber.

It is pure, Isomalto-oligosaccharides made from tapioca starch.

It is has nice sweet flavor and serves as a super low sugar alternative sweetener. It is being sold as an ingredient.

It is a key ingredient in wildly popular Nimbo Chews.

It is gluten free, kosher, vegan, non-GMO. It is made from Tapioca Starch.

We need a product logo and a label concept.

Use color but not too many colors. Must reproduce well in greyscale.

Start by submitting logo. Finish by submitting complete labels in 2 sizes:

4" h x 6" w and 2.5 h x 4" w

The winning designer will be required to make 3 print ready labels (in 2 sizes) for 3 different sized containers of this product. At that point we will provide required text, nutritional info and UPCs.

GOOD LUCK!

Target Market(s)

Health conscious consumers making their own concoctions at home. Mostly for general health. Some due to digestive/intestinal medical conditions.

Industry/Entity Type

Product

Requirements
Must have
• Distinct clear promient product name.
Nice to have
• Great surrounding aesthetic for the entire label/package.
Should not have
• Hard to read font. Extraneous detailed graphic elements.

```html
<!DOCTYPE html>
<html lang="en">
<head>
<meta charset="utf-8">
<title>GlowMallo Label</title>
<link href="https://fonts.googleapis.com/css2?family=Montserrat:wght@500;600;700&family=Quicksand:wght@500;600;700&display=swap" rel="stylesheet">
<style>
  :root {
    --page-bg: #e9e9ea;
    --label-top: #d3dde8;
    --label-bottom: #c3d0dd;
    --ink-dark: #2c3640;
    --ink-mid: #6b7c8c;
    --band: #6c7a88;
    --band-text: #eef2f6;
  }
  * { margin: 0; padding: 0; box-sizing: border-box; }
  html, body {
    width: 1200px; height: 900px; overflow: hidden;
    background: var(--page-bg);
  }
  .canvas {
    width: 1200px; height: 900px;
    display: flex; align-items: center; justify-content: center;
  }
  .label {
    position: relative;
    width: 660px; height: 460px;
    background: linear-gradient(180deg, var(--label-top), var(--label-bottom));
    font-family: "Quicksand", sans-serif;
    color: var(--ink-dark);
    overflow: hidden;
  }
  .brand {
    position: absolute; top: 28px; left: 0; right: 0;
    text-align: center;
    font-family: "Montserrat", sans-serif;
    font-weight: 600; font-size: 42px; line-height: 1.2;
    color: var(--ink-mid);
    letter-spacing: 0.5px;
  }
  .product-name {
    position: absolute; left: 160px; top: 402px;
    transform: rotate(-90deg); transform-origin: left top;
    font-family: "Montserrat", sans-serif;
    font-weight: 500; font-size: 48px; line-height: 1.02;
    white-space: nowrap;
  }
  .product-name .line-1 { display: block; color: var(--ink-mid); letter-spacing: 1px; }
  .product-name .line-2 { display: block; color: var(--ink-dark); font-weight: 600; }
  .details {
    position: absolute; left: 282px; top: 108px; width: 310px;
  }
  .details p {
    font-size: 12.5px; line-height: 1.3; font-weight: 500;
    text-align: justify; margin-bottom: 7px;
  }
  .details .strong { font-weight: 700; }
  .claims {
    list-style: none; margin-top: 10px;
    font-weight: 700; font-size: 25px; line-height: 1.2;
  }
  .count { margin-top: 10px; font-size: 12.5px; font-weight: 500; line-height: 1.3; }
  .count b { font-weight: 700; }
  .band {
    position: absolute; left: 0; right: 0; bottom: 0; height: 34px;
    background: var(--band); color: var(--band-text);
    font-family: "Montserrat", sans-serif; font-weight: 600; font-size: 14px;
    letter-spacing: 1px; display: flex; align-items: center; justify-content: center;
    white-space: nowrap;
  }
</style>
</head>
<body>
  <main class="canvas">
    <section class="label">
      <div class="brand">GlowMallo</div>
      <h1 class="product-name">
        <span class="line-1">PRODUCT</span>
        <span class="line-2">NAME HERE</span>
      </h1>
      <div class="details">
        <p>Lorem ipsum dolor sit amet, consectetur adipisicing elit, sed do eiu smod tempor incididunt ut labore et dolore magna aliqua. Lorem ipsum dolor sit amet, consectetur adipisicing elit, sed do eiu smod tempor incididunt ut labore.</p>
        <p>Lorem ipsum dolor sit amet, consectetur adipisicing elit, <span class="strong">sed do eiu smod tempor incididunt.</span></p>
        <ul class="claims">
          <li>Gluten free</li>
          <li>Kosher</li>
          <li>Vegan</li>
          <li>Non-GMO</li>
        </ul>
        <p class="count">Sed do eiu smod tempor<br><b>Each contains 30 Capsules</b></p>
      </div>
      <div class="band">LOREM IPSUM DOLOR SIT AMET, CONSECTETUR ADIPISICING ELIT, SED DO EIU SMOD</div>
    </section>
  </main>
</body>
</html>
```